Harborline Outpost Registry needs a web design

We are launching a new website and need a web design. The website is going to list every military base and installment around the world with information on each base such as a description of the base, the history of the base, contact information at the base, address, lat/long of the base, and any other relevant information including images of the base. We need a home page with navigation menu and the design of the military base page so that every military base page is formatted the same for the referenced information. We have included an example of the content that may be found on the base page(s). We are also going to have the information available in spanish.

We also wanted to mention we will be building this website in wordpress.

We also wanted to note that in the format of each base page, we will have a frequently asked questions section with answers.

```html
<!DOCTYPE html>
<html lang="en">
<head>
<meta charset="utf-8">
<title>Harborline Outpost Registry</title>
<link href="https://fonts.googleapis.com/css2?family=Titillium+Web:wght@600;700&family=Nunito+Sans:wght@400;600&display=swap" rel="stylesheet">
<style>
:root{
  --accent:#fb5a1c;
  --accent-dark:#c63f0c;
  --ink:#1f1f1f;
  --text:#3b3b3b;
  --white:#fff;
  --band:#efefef;
  --footer:#2b2b2b;
  --border:#e6e6e6;
  --review:#4a7be0;
  --star:#f5b400;
}
*{box-sizing:border-box;margin:0;padding:0}
html,body{width:1200px;height:3498px;overflow:hidden;background:var(--white)}
body{font-family:"Nunito Sans",Arial,sans-serif;color:var(--text);position:relative}
.heading{font-family:"Titillium Web",Arial,sans-serif;font-weight:700;text-transform:uppercase;color:var(--ink)}
.btn{background:var(--accent);color:var(--white);font-size:16px;font-weight:600;display:flex;align-items:center;justify-content:center;border:none}

.hero{position:absolute;left:0;top:0;width:1200px;height:514px;
  background:radial-gradient(circle at 305px 120px,#ffe9a0 0,#f8b52a 60px,#d9841b 180px,rgba(120,60,15,0) 420px),
  linear-gradient(180deg,#c8731c 0%,#a65416 45%,#5b2a0d 75%,#2a1408 100%)}
.nav{position:absolute;left:113px;right:113px;top:22px;height:36px;display:flex;align-items:center}
.logo{font-family:"Titillium Web",Arial,sans-serif;font-weight:700;font-size:25px;color:var(--white);text-transform:uppercase}
.menu{margin-left:auto;display:flex;gap:36px;list-style:none;font-size:16px;color:var(--white);margin-right:40px}
.flag{width:30px;height:30px}
.hero-title{position:absolute;top:248px;width:100%;text-align:center;font-size:41px;color:var(--white)}
.search{position:absolute;left:330px;top:334px;width:540px;height:43px;display:flex}
.search-field{flex:1;background:var(--white);display:flex;align-items:center;padding-left:20px;gap:12px;font-size:15px;color:#666}
.search .btn{width:109px}

.featured-title{position:absolute;left:110px;top:582px;font-size:40px}
.cards{position:absolute;left:111px;top:683px;width:976px}
.card{height:274px;margin-bottom:43.5px;display:flex;background:var(--white);border:1px solid var(--border);box-shadow:0 2px 6px rgba(0,0,0,.08);position:relative}
.card-photo{width:274px;height:100%;flex:none}
.card-body{padding:32px 0 0 41px}
.card-title{font-size:25px;line-height:1.1;font-weight:600}
.card-sub{font-size:19px;margin-top:10px}
.info{display:flex;align-items:center;gap:14px;font-size:19px;color:var(--ink)}
.info.phone{margin-top:30px}
.info.pin{margin-top:18px}
.coords{font-size:19px;margin:14px 0 0 34px}
.card .btn{position:absolute;right:32px;top:38px;width:132px;height:44px}
.load{position:absolute;left:498px;top:2619px;width:204px;height:43px}

.testimonials{position:absolute;left:0;top:2728px;width:1200px;height:541px;background:var(--band)}
.testimonials .heading{position:absolute;top:72px;width:100%;text-align:center;font-size:40px}
.quote-card{position:absolute;top:200px;width:429px;height:268px;background:var(--white);box-shadow:0 2px 6px rgba(0,0,0,.06);padding:58px 25px 0}
.quote-badge{position:absolute;left:21px;top:-35px;width:80px;height:80px}
.quote-name{font-size:20px;font-weight:400;color:var(--ink)}
.quote-text{font-size:16px;line-height:28px;margin-top:10px}
.review{margin-top:14px;display:flex;flex-direction:column;gap:2px}
.review-name{font-size:17px;font-weight:600;color:var(--review)}

.footer{position:absolute;left:0;top:3269px;width:1200px;height:229px;background:var(--footer);color:var(--white);text-align:center}
.footer .logo{position:absolute;top:50px;width:100%;font-size:27px}
.footer-menu{position:absolute;top:100px;width:100%;display:flex;justify-content:center;gap:36px;list-style:none;font-size:16px}
.copyright{position:absolute;top:143px;width:100%;font-size:16px}
</style>
</head>
<body>
<svg width="0" height="0" style="position:absolute">
  <defs>
    <path id="icon-phone" fill="#fb5a1c" d="M6.6 10.8a15 15 0 006.6 6.6l2.2-2.2a1 1 0 011-.25 11.4 11.4 0 003.6.6 1 1 0 011 1V20a1 1 0 01-1 1A17 17 0 013 4a1 1 0 011-1h3.5a1 1 0 011 1c0 1.25.2 2.45.6 3.6a1 1 0 01-.25 1z"/>
    <path id="icon-pin" fill="#fb5a1c" d="M12 2a7 7 0 00-7 7c0 5.2 7 13 7 13s7-7.8 7-13a7 7 0 00-7-7zm0 9.5A2.5 2.5 0 1112 6.5a2.5 2.5 0 010 5z"/>
    <g id="quote-mark">
      <circle cx="40" cy="42" r="38" fill="#c63f0c"/>
      <circle cx="40" cy="38" r="38" fill="#fb5a1c"/>
      <g fill="#fff">
        <circle cx="29" cy="33" r="8"/><path d="M35 35q0 14-14 19l-2-4q8-4 8-11z"/>
        <circle cx="51" cy="33" r="8"/><path d="M57 35q0 14-14 19l-2-4q8-4 8-11z"/>
      </g>
    </g>
    <g id="stars" fill="#f5b400"><circle cx="10" cy="4" r="3"/><circle cx="17" cy="4" r="3"/><circle cx="24" cy="4" r="3"/><circle cx="31" cy="4" r="3"/><circle cx="38" cy="4" r="3"/></g>
  </defs>
</svg>

<header class="hero" role="img" aria-label="Silhouettes of soldiers walking across a desert at sunset with a helicopter overhead">
  <nav class="nav">
    <div class="logo">Harborline Outpost Registry</div>
    <ul class="menu"><li>Home</li><li>About</li><li>Military Base</li><li>Blog</li><li>Contact</li></ul>
    <svg class="flag" viewBox="0 0 30 30" aria-label="Language">
      <defs><clipPath id="c"><circle cx="15" cy="15" r="14"/></clipPath></defs>
      <g clip-path="url(#c)">
        <rect width="30" height="30" fill="#fff"/>
        <rect y="2" width="30" height="3" fill="#d22"/><rect y="8" width="30" height="3" fill="#d22"/>
        <rect y="14" width="30" height="3" fill="#d22"/><rect y="20" width="30" height="3" fill="#d22"/>
        <rect y="26" width="30" height="3" fill="#d22"/>
        <rect width="15" height="14" fill="#2c3d8f"/>
      </g>
      <circle cx="15" cy="15" r="14" fill="none" stroke="#fff" stroke-width="2"/>
    </svg>
  </nav>
  <h1 class="heading hero-title">Harborline Outpost Registry</h1>
  <form class="search">
    <div class="search-field">
      <svg width="16" height="16" viewBox="0 0 16 16"><circle cx="6.5" cy="6.5" r="5" fill="none" stroke="#999" stroke-width="1.5"/><path d="M10 10l5 5" stroke="#999" stroke-width="1.5"/></svg>
      Search Military Base
    </div>
    <div class="btn">Search</div>
  </form>
</header>

<h2 class="heading featured-title">Featured Military Base</h2>

<section class="cards">
  <article class="card">
    <div class="card-photo" role="img" aria-label="Soldiers and helicopter silhouetted against a sunset" style="background:linear-gradient(160deg,#7d9ac0,#e4a064 55%,#2b1d16)"></div>
    <div class="card-body">
      <h3 class="heading card-title">Fort Calder Outpost</h3>
      <p class="card-sub">History, Facilities, and Support Services</p>
      <p class="info phone"><svg width="20" height="20" viewBox="0 0 24 24"><use href="#icon-phone"/></svg>(555) 014-3710</p>
      <p class="info pin"><svg width="20" height="20" viewBox="0 0 24 24"><use href="#icon-pin"/></svg>Calder Ridge, KY, United States</p>
      <p class="coords">Latitude: 41.2235° N Longitude: 79.4468° W DSN</p>
    </div>
    <div class="btn">Learn More</div>
  </article>
  <article class="card">
    <div class="card-photo" role="img" aria-label="Soldier in combat gear holding a rifle in a forest" style="background:linear-gradient(160deg,#6f7a4e,#8b8663 50%,#3f3c2c)"></div>
    <div class="card-body">
      <h3 class="heading card-title">Lorem ipsum dolor sit amet</h3>
      <p class="card-sub">History, Facilities, and Support Services</p>
      <p class="info phone"><svg width="20" height="20" viewBox="0 0 24 24"><use href="#icon-phone"/></svg>+1888-888-8888</p>
      <p class="info pin"><svg width="20" height="20" viewBox="0 0 24 24"><use href="#icon-pin"/></svg>Lorem ipsum dolor sit amet</p>
      <p class="coords">Latitude: 41.2235° N Longitude: 79.4468° W DSN</p>
    </div>
    <div class="btn">Learn More</div>
  </article>
  <article class="card">
    <div class="card-photo" role="img" aria-label="Soldiers walking away on a dusty desert track" style="background:linear-gradient(180deg,#e9e1cf,#b99f77 55%,#7d6648)"></div>
    <div class="card-body">
      <h3 class="heading card-title">Lorem ipsum dolor sit amet</h3>
      <p class="card-sub">History, Facilities, and Support Services</p>
      <p class="info phone"><svg width="20" height="20" viewBox="0 0 24 24"><use href="#icon-phone"/></svg>+1888-888-8888</p>
      <p class="info pin"><svg width="20" height="20" viewBox="0 0 24 24"><use href="#icon-pin"/></svg>Lorem ipsum dolor sit amet</p>
      <p class="coords">Latitude: 41.2235° N Longitude: 79.4468° W DSN</p>
    </div>
    <div class="btn">Learn More</div>
  </article>
  <article class="card">
    <div class="card-photo" role="img" aria-label="Soldiers operating a drone in the desert" style="background:linear-gradient(160deg,#a9c0d3,#c8b392 50%,#8a7a62)"></div>
    <div class="card-body">
      <h3 class="heading card-title">Lorem ipsum dolor sit amet</h3>
      <p class="card-sub">History, Facilities, and Support Services</p>
      <p class="info phone"><svg width="20" height="20" viewBox="0 0 24 24"><use href="#icon-phone"/></svg>+1888-888-8888</p>
      <p class="info pin"><svg width="20" height="20" viewBox="0 0 24 24"><use href="#icon-pin"/></svg>Lorem ipsum dolor sit amet</p>
      <p class="coords">Latitude: 41.2235° N Longitude: 79.4468° W DSN</p>
    </div>
    <div class="btn">Learn More</div>
  </article>
  <article class="card">
    <div class="card-photo" role="img" aria-label="Recruits running a tire obstacle course" style="background:linear-gradient(180deg,#9a9486,#6f6a5e 55%,#2a2824)"></div>
    <div class="card-body">
      <h3 class="heading card-title">Lorem ipsum dolor sit amet</h3>
      <p class="card-sub">History, Facilities, and Support Services</p>
      <p class="info phone"><svg width="20" height="20" viewBox="0 0 24 24"><use href="#icon-phone"/></svg>+1888-888-8888</p>
      <p class="info pin"><svg width="20" height="20" viewBox="0 0 24 24"><use href="#icon-pin"/></svg>Lorem ipsum dolor sit amet</p>
      <p class="coords">Latitude: 41.2235° N Longitude: 79.4468° W DSN</p>
    </div>
    <div class="btn">Learn More</div>
  </article>
  <article class="card">
    <div class="card-photo" role="img" aria-label="Military helicopters parked on an airfield at dusk" style="background:linear-gradient(180deg,#3f6b78,#8a9a7a 50%,#c9a45a 75%,#3a3022)"></div>
    <div class="card-body">
      <h3 class="heading card-title">Lorem ipsum dolor sit amet</h3>
      <p class="card-sub">History, Facilities, and Support Services</p>
      <p class="info phone"><svg width="20" height="20" viewBox="0 0 24 24"><use href="#icon-phone"/></svg>+1888-888-8888</p>
      <p class="info pin"><svg width="20" height="20" viewBox="0 0 24 24"><use href="#icon-pin"/></svg>Lorem ipsum dolor sit amet</p>
      <p class="coords">Latitude: 41.2235° N Longitude: 79.4468° W DSN</p>
    </div>
    <div class="btn">Learn More</div>
  </article>
</section>

<div class="btn load">Load More</div>

<section class="testimonials">
  <h2 class="heading">Client Testimonials</h2>
  <article class="quote-card" style="left:141px">
    <svg class="quote-badge" viewBox="0 0 80 80"><use href="#quote-mark"/></svg>
    <h3 class="quote-name">Marcus Hale</h3>
    <p class="quote-text">Ut enim ad minima veniam, quis nostr exercit lore ationem ullam corporis suscipit laborim, nisit utips aliquid ex ea commodi consequatur.</p>
    <div class="review"><span class="review-name">Reviewly</span><svg width="44" height="8" viewBox="0 0 44 8"><use href="#stars"/></svg></div>
  </article>
  <article class="quote-card" style="left:630px">
    <svg class="quote-badge" viewBox="0 0 80 80"><use href="#quote-mark"/></svg>
    <h3 class="quote-name">Marcus Hale</h3>
    <p class="quote-text">Ut enim ad minima veniam, quis nostr exercit lore ationem ullam corporis suscipit laborim, nisit utips aliquid ex ea commodi consequatur.</p>
    <div class="review"><span class="review-name">Reviewly</span><svg width="44" height="8" viewBox="0 0 44 8"><use href="#stars"/></svg></div>
  </article>
</section>

<footer class="footer">
  <div class="logo">Harborline Outpost Registry</div>
  <ul class="footer-menu"><li>Home</li><li>About</li><li>Military Base</li><li>Blog</li><li>Contact</li></ul>
  <p class="copyright">2023 Harborline Outpost Registry. All Rights Reserved.</p>
</footer>
</body>
</html>
```